Email Signature and a letter head

I need a professional email signature and a letter head for letters sent by post. I've attached my logo and a signature i am currently using. Current letter head is also attached.

Target Market(s)

Accounting Clients

Industry/Entity Type

Public Accounting

Font styles to use
Sans Serif

Colors

Designer to choose colors to be used in the design.

Requirements
Must have
• My logo, RM Logo, Lumo Logo, Tax Agent logo. All attached.
• All my credentials - examples in the attached documents

```html
<!DOCTYPE html>
<html lang="en">
<head>
<meta charset="utf-8">
<title>Summit Ledger – Letterhead and Email Signature</title>
<link rel="stylesheet" href="https://fonts.googleapis.com/css2?family=Libre+Baskerville&family=Open+Sans:wght@400;600&display=swap">
<style>
  :root {
    --backdrop: #b3b3b3;
    --paper: #f8f8f8;
    --gold: #a88a2c;
    --ink: #333333;
    --watermark: #ececec;
    --teal-light: #1aa3c9;
    --teal-dark: #13708a;
    --badge-red: #d9432f;
    --badge-lime: #c9d82a;
    --eco-green: #3f9a35;
    --note-blue: #3a4a7a;
    --frame: #cfcfcf;
  }
  * { margin: 0; padding: 0; box-sizing: border-box; }
  html, body { width: 1200px; height: 872px; overflow: hidden; }
  body { background: var(--backdrop); position: relative; font-family: "Libre Baskerville", Georgia, serif; color: var(--ink); }

  .letterhead { position: absolute; left: 182px; top: 145px; width: 411px; height: 582px; background: var(--paper); }
  .brand { position: absolute; text-align: center; color: var(--gold); }
  .brand-mark { display: block; margin: 0 auto; border: 2px solid var(--gold); border-radius: 50%; }
  .brand-name { display: block; font-size: 10px; letter-spacing: 0.6px; white-space: nowrap; text-transform: uppercase; }
  .brand-sub { display: block; font-family: "Open Sans", sans-serif; font-size: 4.6px; letter-spacing: 1.6px; text-transform: uppercase; }
  .letterhead .brand { left: 18px; top: 26px; width: 114px; }
  .letterhead .brand-mark { width: 44px; height: 44px; margin-bottom: 6px; }

  .contact { position: absolute; border-left: 1.5px solid var(--gold); padding-left: 10px; }
  .contact-name { color: var(--gold); font-size: 10.5px; white-space: nowrap; }
  .contact-ids { font-size: 5.2px; margin: 1px 0 4px; white-space: nowrap; }
  .contact-ids .label { color: var(--gold); }
  .contact-line { font-size: 5.2px; line-height: 7.2px; white-space: nowrap; display: flex; align-items: center; gap: 3px; }
  .contact-line svg { width: 4.5px; height: 4.5px; fill: var(--gold); flex: none; }
  .letterhead .contact { left: 244px; top: 37px; height: 52px; }

  .watermark { position: absolute; left: 59px; top: 185px; }

  .footer-rule { position: absolute; top: 558px; height: 2px; background: var(--gold); }
  .footer-rule.left { left: 0; width: 120px; }
  .footer-rule.right { left: 291px; width: 120px; }
  .badges { position: absolute; display: flex; align-items: center; }
  .badge { border-radius: 50%; flex: none; }
  .badge-lumo { background: var(--teal-light); }
  .badge-lumo-partner { background: var(--teal-dark); }
  .badge-rm { background: none; border: 2.5px solid var(--badge-red); border-right-color: var(--gold); }
  .badge-tax { background: var(--badge-lime); border: 1.5px solid #888; }
  .tax-label { font-family: "Open Sans", sans-serif; font-weight: 600; color: #222; white-space: nowrap; }
  .letterhead .badges { left: 129px; top: 546px; gap: 0; }
  .letterhead .badge-lumo, .letterhead .badge-lumo-partner { width: 26px; height: 26px; }
  .letterhead .badge-lumo-partner { margin-left: 0; }
  .letterhead .badge-rm { width: 18px; height: 18px; margin-left: 14px; }
  .letterhead .badge-tax { width: 26px; height: 26px; margin-left: 20px; }
  .letterhead .tax-label { font-size: 4.6px; line-height: 5.4px; margin-left: 2px; }

  .signature { position: absolute; left: 633px; top: 423px; width: 370px; height: 90px; background: var(--paper); border: 1px solid var(--frame); }
  .signature .brand { left: 10px; top: 18px; width: 94px; }
  .signature .brand-mark { width: 36px; height: 36px; margin-bottom: 4px; }
  .signature .brand-name { font-size: 8.6px; }
  .signature .brand-sub { font-size: 4px; }
  .signature .contact { left: 118px; top: 22px; height: 52px; }
  .signature .badges { left: 322px; top: 12px; flex-direction: column; gap: 6px; }
  .sig-lumo-row { display: flex; }
  .signature .badge-lumo, .signature .badge-lumo-partner { width: 17px; height: 17px; }
  .signature .badge-rm { width: 13px; height: 13px; }
  .sig-tax-row { display: flex; align-items: center; margin-left: -4px; }
  .signature .badge-tax { width: 17px; height: 17px; }
  .signature .tax-label { font-size: 3.8px; line-height: 4.4px; margin-left: 2px; }

  .disclaimer { position: absolute; left: 635px; top: 518px; width: 340px; font-family: "Open Sans", sans-serif; font-size: 5.2px; line-height: 7.4px; color: var(--note-blue); }
  .eco-note { position: absolute; left: 644px; top: 542px; display: flex; align-items: center; gap: 16px; font-family: "Open Sans", sans-serif; font-size: 5.4px; color: var(--eco-green); }
  .eco-note svg { width: 14px; height: 12px; fill: var(--eco-green); }
</style>
</head>
<body>

<section class="letterhead" aria-label="Letterhead">
  <div class="brand">
    <span class="brand-mark"></span>
    <span class="brand-name">Summit Ledger</span>
    <span class="brand-sub">Business Services</span>
  </div>

  <div class="contact">
    <p class="contact-name">Marlena Cross RM BBus.</p>
    <p class="contact-ids"><span class="label">ABN:</span> 51 302 774 618 <span class="label">&nbsp;|&nbsp; TAN:</span> 307 118 42</p>
    <p class="contact-line"><svg viewBox="0 0 10 10"><rect x="2" y="1" width="6" height="8" rx="1"/></svg>0400123987</p>
    <p class="contact-line"><svg viewBox="0 0 10 10"><circle cx="5" cy="5" r="4"/></svg>www.summitledgerservices.com.au</p>
    <p class="contact-line"><svg viewBox="0 0 10 10"><rect x="0.5" y="2" width="9" height="6"/></svg>marlena@summitledgerservices.com.au</p>
    <p class="contact-line"><svg viewBox="0 0 10 10"><path d="M5 0a3.5 3.5 0 0 1 3.5 3.5C8.5 6 5 10 5 10S1.5 6 1.5 3.5A3.5 3.5 0 0 1 5 0z"/></svg>12 Harbour Lane Seaford North VIC 3198</p>
  </div>

  <svg class="watermark" width="294" height="294" viewBox="0 0 294 294" aria-hidden="true">
    <circle cx="147" cy="147" r="143" fill="none" stroke="var(--watermark)" stroke-width="5"/>
  </svg>

  <div class="footer-rule left"></div>
  <div class="footer-rule right"></div>
  <div class="badges">
    <span class="badge badge-lumo"></span>
    <span class="badge badge-lumo-partner"></span>
    <span class="badge badge-rm"></span>
    <span class="badge badge-tax"></span>
    <span class="tax-label">Tax Agent<br>20481736</span>
  </div>
</section>

<section class="signature" aria-label="Email signature">
  <div class="brand">
    <span class="brand-mark"></span>
    <span class="brand-name">Summit Ledger</span>
    <span class="brand-sub">Business Services</span>
  </div>

  <div class="contact">
    <p class="contact-name">Marlena Cross RM BBus.</p>
    <p class="contact-ids"><span class="label">ABN:</span> 51 302 774 618 <span class="label">&nbsp;|&nbsp; TAN:</span> 307 118 42</p>
    <p class="contact-line"><svg viewBox="0 0 10 10"><rect x="2" y="1" width="6" height="8" rx="1"/></svg>0400123987</p>
    <p class="contact-line"><svg viewBox="0 0 10 10"><circle cx="5" cy="5" r="4"/></svg>www.summitledgerservices.com.au</p>
    <p class="contact-line"><svg viewBox="0 0 10 10"><rect x="0.5" y="2" width="9" height="6"/></svg>marlena@summitledgerservices.com.au</p>
    <p class="contact-line"><svg viewBox="0 0 10 10"><path d="M5 0a3.5 3.5 0 0 1 3.5 3.5C8.5 6 5 10 5 10S1.5 6 1.5 3.5A3.5 3.5 0 0 1 5 0z"/></svg>12 Harbour Lane Seaford North VIC 3198</p>
  </div>

  <div class="badges">
    <div class="sig-lumo-row">
      <span class="badge badge-lumo"></span>
      <span class="badge badge-lumo-partner"></span>
    </div>
    <span class="badge badge-rm"></span>
    <div class="sig-tax-row">
      <span class="badge badge-tax"></span>
      <span class="tax-label">Tax Agent<br>20481736</span>
    </div>
  </div>
</section>

<p class="disclaimer">This e-mail and its attachments are confidential and privileged. Any unauthorised use is expressly prohibited. If you receive this e-mail in error please contact us, then delete the e-mail.</p>

<p class="eco-note">
  <svg viewBox="0 0 14 12" aria-hidden="true"><path d="M7 0L11 5H9V8H5V5H3z"/><rect x="0" y="9" width="14" height="3"/></svg>
  Please consider the environment before printing this e-mail notice.
</p>

</body>
</html>
```